A 'new law' boutique Australian law firm that provides specialist employment law and people managem

We value helping clients create results with respect workplaces. What differentiates us is we provide actionable training in understanding and dealing with people and ensure legal compliance fits with this approach. We would like a fresh approach to our training overview documents that we currently use in our current law firm (6 attached). Please use pictures, symbols etc consistent with our non-traditional law approach that captures the approach of each training session.. Attached is the logo and draft letterhead for Birchwell Legal which will launch soon.

Target Market(s)

HR Managers and in-house lawyers (non employment specialists) in mid-large Australian companies that are progressive with a relationship based approach to managing employee behaviours and disputes.

Industry/Entity Type

Human Resource

Font styles to use
Sans Serif

Colors
3176b5
33a6d7

Requirements
Must have
• 1 or 2 page PDF for each of the 6 documents that the wording supplied goes into your design which will be pretty similar as we want consistency with our documents

```html
<!DOCTYPE html>
<html lang="en">
<head>
<meta charset="utf-8">
<title>Contact Officer Training – Birchwell Legal</title>
<link rel="stylesheet" href="https://fonts.googleapis.com/css2?family=Titillium+Web:wght@700;900&family=Roboto:wght@400;700&display=swap">
<style>
  :root {
    --brand-blue: #1173be;
    --brand-line: #2b8cd0;
    --ink: #222222;
    --slate: #6d6e71;
    --charcoal: #3a3b3d;
    --cell-key: #dcdddf;
    --cell-body: #c3c4c6;
    --paper: #ffffff;
  }
  * { margin: 0; padding: 0; box-sizing: border-box; }
  html, body { width: 913px; height: 1200px; overflow: hidden; background: var(--paper); }
  .flyer { position: relative; width: 913px; height: 1200px; background: var(--paper); font-family: "Roboto", Arial, sans-serif; color: var(--ink); overflow: hidden; }

  .hero { position: absolute; left: 0; top: 0; width: 913px; height: 485px; }
  .title { position: absolute; left: 44px; top: 40px; font-family: "Titillium Web", Arial, sans-serif; font-weight: 900; color: var(--brand-blue); line-height: 1; }
  .title .line-small { display: block; font-size: 39px; letter-spacing: -0.5px; }
  .title .line-large { display: block; font-size: 78px; letter-spacing: -1px; margin-top: -6px; }

  .need-heading { position: absolute; left: 35px; top: 258px; font-family: "Titillium Web", Arial, sans-serif; font-weight: 700; font-size: 28px; color: #fff; }
  .need-col { position: absolute; top: 311px; color: #fff; font-size: 12.6px; line-height: 15.5px; }
  .need-col p + p { margin-top: 15.5px; }
  .need-col.left { left: 35px; width: 372px; }
  .need-col.right { left: 456px; width: 372px; }

  .section-heading { position: absolute; font-family: "Titillium Web", Arial, sans-serif; font-weight: 700; font-size: 28px; line-height: 1; }
  .overview-heading { left: 45px; top: 502px; color: var(--slate); }

  .overview { position: absolute; left: 36px; top: 538px; width: 840px; border-collapse: collapse; font-size: 10.2px; line-height: 12.6px; }
  .overview td { border: 2px solid #fff; vertical-align: middle; }
  .overview .topic { width: 228px; background: var(--cell-key); padding: 0 26px; }
  .overview .detail { background: var(--cell-body); padding: 0 24px; }

  .outcomes-heading { left: 46px; top: 999px; color: var(--brand-blue); }
  .outcomes-intro { position: absolute; left: 46px; top: 1034px; font-size: 12.2px; font-weight: 700; }
  .outcomes-list { position: absolute; left: 46px; top: 1056px; list-style: none; font-size: 12.3px; line-height: 15.5px; }

  .brand { position: absolute; left: 616px; top: 992px; width: 250px; text-align: center; }
  .brand-dot { display: block; width: 40px; height: 40px; border-radius: 50%; background: var(--brand-blue); margin: 0 auto 12px; }
  .brand-name { font-family: "Roboto", Arial, sans-serif; font-weight: 700; font-size: 26px; color: var(--charcoal); line-height: 1; white-space: nowrap; }

  .contact-band { position: absolute; left: 0; top: 0; }
  .contact { position: absolute; left: 591px; top: 1120px; width: 300px; text-align: center; color: #fff; font-size: 12px; font-weight: 700; line-height: 16px; font-style: normal; white-space: nowrap; }
</style>
</head>
<body>
<main class="flyer">
  <svg class="hero" width="913" height="485" viewBox="0 0 913 485">
    <defs>
      <linearGradient id="photoTone" x1="0" y1="0" x2="1" y2="0">
        <stop offset="0" stop-color="#ffffff"/>
        <stop offset="0.4" stop-color="#eef1f4"/>
        <stop offset="0.7" stop-color="#c9cdd3"/>
        <stop offset="1" stop-color="#5e74b8"/>
      </linearGradient>
    </defs>
    <rect role="img" aria-label="Photo of people at a meeting table taking notes with a pen" x="0" y="0" width="913" height="300" fill="url(#photoTone)"/>
    <rect x="0" y="30" width="400" height="120" fill="#ffffff" opacity="0.9"/>
    <path d="M0 188 C 200 205, 360 250, 520 246 C 690 240, 800 175, 913 140" fill="none" stroke="var(--charcoal)" stroke-width="10" opacity="0.85"/>
    <path d="M0 202 C 200 222, 350 270, 520 262 C 690 252, 800 190, 913 150 L913 485 L0 485 Z" fill="var(--brand-blue)"/>
    <path d="M0 202 C 200 222, 350 270, 520 262 C 690 252, 800 190, 913 150" fill="none" stroke="var(--brand-line)" stroke-width="4"/>
  </svg>

  <h1 class="title"><span class="line-small">CONTACT OFFICER</span><span class="line-large">TRAINING</span></h1>

  <h2 class="need-heading">TRAINING NEED</h2>
  <div class="need-col left">
    <p>Unlawful or inappropriate behavior in the workplace that is left unaddressed can impact on productivity and employee retention.&nbsp; Claims can be costly in terms of time and money as well as the impact on mental health from being involved in uncomfortable adversarial processes.</p>
    <p>Clear policies and procedures explaining the organisation's workplace behavior expectations and how grievances will be managed are a minimum compliance requirement.</p>
  </div>
  <div class="need-col right">
    <p>The challenge is ensuring that employees understand the directions contained in those policies, what is unlawful and inappropriate behaviour and the options available to address those behaviours if they experience them or engage in them.</p>
    <p>Well trained Contact Officers provide another resource to assist the organisation to provide a safe and respectful workplace.</p>
  </div>

  <h2 class="section-heading overview-heading">OVERVIEW</h2>
  <table class="overview">
    <tr style="height:59px"><td class="topic">Discrimination</td><td class="detail">What is direct and indirect discrimination?&nbsp; What are the prescribed attributes?<br>What are the exceptions to the general rules.<br>Practical examples of behaviour that may be discriminatory.</td></tr>
    <tr style="height:61px"><td class="topic">Harassment</td><td class="detail">What is harassment?&nbsp; Are protected attributes relevant to harassment? What is the difference between harassment and sexual harassment?&nbsp; How does the reasonable person test work in relation to harassment? Practical examples of behaviour that may be harassment or sexual harassment.</td></tr>
    <tr style="height:60px"><td class="topic">Bullying</td><td class="detail">What is bullying. Explore how bullying differs to discrimination or inappropriate behaviour. Performance Management - when it will and will not be bullying. Is all workplace conflict bullying?<br>Practical examples of behaviour that may be bullying.</td></tr>
    <tr style="height:31px"><td class="topic">Victimisation and Vilification</td><td class="detail">What is victimisation? What is Vilification?</td></tr>
    <tr style="height:61px"><td class="topic">Adverse Action</td><td class="detail">What is adverse action and how does it differ to other unlawful behaviour? What is a workplace right?<br>When is it lawful to terminate employment because of an employee's absence?<br>How are the protected attributes relevant to adverse action?</td></tr>
    <tr style="height:61px"><td class="topic">The Contact Officer's role</td><td class="detail">How to perform your role when approached by an employee – the 6 step approach. What not to do.<br>What are the obligations with regard to Confidentiality?</td></tr>
    <tr style="height:62px"><td class="topic">Grievance Options</td><td class="detail">Explore the options of complaint management - self management, internal informal management, formal internal management.&nbsp; How do they compare and what are the advantages and disadvantages of each approach.&nbsp; Is doing nothing an option? External options – advantages and disadvantages.&nbsp; Who decides which option?</td></tr>
    <tr style="height:36px"><td class="topic">Test Learning</td><td class="detail">Role play, group discussion</td></tr>
  </table>

  <h2 class="section-heading outcomes-heading">LEARNING OUTCOMES</h2>
  <p class="outcomes-intro">Training will enable participants to perform their role of Contact Officer and to understand:</p>
  <ul class="outcomes-list">
    <li>1 The role and responsibilities of a Contact Officer</li>
    <li>2 What amounts to unlawful workplace behaviour</li>
    <li>3 What is considered inappropriate behaviour in our workplace</li>
    <li>4 How to apply understanding unlawful/inappropriate behaviour to common scenarios</li>
    <li>5 How to address and resolve grievances early</li>
    <li>6 Options to resolve grievances internally and the Contact Officer role</li>
    <li>7 External options and their pros and cons for resolving grievances</li>
  </ul>

  <div class="brand">
    <span class="brand-dot"></span>
    <div class="brand-name">Birchwell Legal</div>
  </div>

  <svg class="contact-band" width="913" height="1200" viewBox="0 0 913 1200" aria-hidden="true">
    <polygon points="598,1107 913,1107 913,1200 521,1200" fill="var(--brand-blue)"/>
  </svg>
  <address class="contact">
    www.birchwell.com.au<br>
    58 Harrow Lane, Kingsford Park and Level 4,<br>
    210 Wattle St. Brookvale.<br>
    Ph: 1300 55 0192 | Email: info@birchwell.com.au
  </address>
</main>
</body>
</html>
```